Indy Film Production Company/Studio

We need a business card designed from an existing logo. We are a digital studio/production company that caters to creating genre entertainment, like Action, Horror, and martial arts. The card along with the logo will be used to Brand the company from letter heads to banners. The design will also be used for postcards and Brochures. It should be professional and masculine.
Updates

Thank you to all the designers who have participated. I'm narrowing down who it will be. Thank you again.

Target Market(s)

Investors, Networks, Producers, and actors

Industry/Entity Type

Film Production

Contact Information for Business Card

Teodoro Valbuena
Producer/Writer/Director
www.kestrelpicturehouse.example

Requirements
Must have
• Website address, Facebook icon and Twitter icon possibly in the back of the card.
Nice to have
• Logline of Company: Follow The Action.

```html
<!DOCTYPE html>
<html lang="en">
<head>
<meta charset="utf-8">
<title>Kestrel Picture House — Business Card</title>
<link href="https://fonts.googleapis.com/css2?family=Open+Sans:wght@400;700&display=swap" rel="stylesheet">
<style>
  :root {
    --backdrop: #2a2a2a;
    --card: #121212;
    --card-panel: #161616;
    --ink: #f2f2f2;
    --ink-soft: #cfcfcf;
    --divider: #2c2c2c;
  }
  * { box-sizing: border-box; margin: 0; padding: 0; }
  html, body {
    width: 1200px; height: 900px; overflow: hidden;
    background: var(--backdrop);
    font-family: "Open Sans", Arial, sans-serif;
    color: var(--ink);
  }
  .sheet {
    position: relative; width: 1200px; height: 900px;
    display: flex; align-items: center; justify-content: center; gap: 60px;
  }
  .card {
    position: relative; width: 500px; height: 286px;
    background: var(--card); border-radius: 18px;
    box-shadow: 0 10px 30px rgba(0,0,0,.45);
    overflow: hidden;
  }
  .wordmark {
    display: flex; flex-direction: column; align-items: center;
    font-weight: 700; color: var(--ink); text-transform: uppercase;
    line-height: 1;
  }
  .wordmark__initials { font-size: 66px; letter-spacing: 2px; }
  .wordmark__name { font-size: 15px; letter-spacing: 1.5px; margin-top: 6px; }

  .card--front { display: flex; }
  .front__brand {
    width: 54%; display: flex; align-items: center; justify-content: center;
  }
  .front__details {
    width: 46%; background: var(--card-panel);
    border-left: 1px solid var(--divider);
    border-radius: 18px 0 0 18px;
    padding: 40px 12px 0 18px;
  }
  .person__name { font-size: 17px; font-weight: 400; }
  .person__role { font-size: 11px; color: var(--ink-soft); margin-top: 1px; }
  .address { font-size: 11px; color: var(--ink-soft); margin-top: 14px; line-height: 1.4; }
  .contact-list { list-style: none; margin-top: 12px; }
  .contact-list li {
    display: flex; align-items: center; gap: 7px;
    font-size: 11px; color: var(--ink-soft); line-height: 1.5;
    white-space: nowrap;
  }
  .contact-list svg { width: 10px; height: 10px; fill: none; stroke: var(--ink); stroke-width: 2; flex: none; }
  .contact-list .icon-fill { fill: var(--ink); stroke: none; }

  .card--back { display: flex; flex-direction: column; align-items: center; justify-content: center; }
  .social-row {
    position: absolute; left: 0; right: 0; bottom: 22px;
    display: flex; justify-content: center; gap: 22px;
    list-style: none; font-size: 11px; color: var(--ink-soft);
  }
  .social-row li { display: flex; align-items: center; gap: 6px; white-space: nowrap; }
  .social-dot { width: 10px; height: 10px; border-radius: 50%; background: var(--ink); flex: none; }
</style>
</head>
<body>
<main class="sheet">
  <section class="card card--front" aria-label="Business card front">
    <div class="front__brand">
      <div class="wordmark">
        <span class="wordmark__initials">KPH</span>
        <span class="wordmark__name">Kestrel Picture House</span>
      </div>
    </div>
    <div class="front__details">
      <h1 class="person__name">Teodoro Valbuena</h1>
      <p class="person__role">Producer/Writer/Director</p>
      <p class="address">12345, Address Goes Here<br>Country Name, 123456.</p>
      <ul class="contact-list">
        <li>
          <svg viewBox="0 0 10 10" aria-hidden="true"><path class="icon-fill" d="M2 0.5 L3.6 0.5 L4.2 3 L3 3.8 Q4 6 6.2 7 L7 5.8 L9.5 6.4 L9.5 8 Q9.5 9.5 8 9.5 Q1 9 0.5 2 Q0.5 0.5 2 0.5Z"/></svg>
          044-555 010 789
        </li>
        <li>
          <svg viewBox="0 0 10 10" aria-hidden="true"><rect x="0.5" y="1.5" width="9" height="7" class="icon-fill"/><path d="M1 2.2 L5 5.5 L9 2.2" stroke="#161616" stroke-width="1.2"/></svg>
          info@kestrelpicturehouse.example
        </li>
        <li>
          <svg viewBox="0 0 10 10" aria-hidden="true"><path d="M4.5 5.5 L6 4 M3.5 4.2 L2 5.7 Q0.8 7 2 8.2 Q3.2 9.3 4.4 8 L5.8 6.6 M4.2 3.4 L5.6 2 Q6.8 0.8 8 2 Q9.2 3.2 8 4.4 L6.6 5.8"/></svg>
          www.kestrelpicturehouse.example
        </li>
      </ul>
    </div>
  </section>

  <section class="card card--back" aria-label="Business card back">
    <div class="wordmark">
      <span class="wordmark__initials">KPH</span>
      <span class="wordmark__name">Kestrel Picture House</span>
    </div>
    <ul class="social-row" aria-label="Social profiles">
      <li><span class="social-dot" aria-hidden="true"></span>/kestrelpicturehouse</li>
      <li><span class="social-dot" aria-hidden="true"></span>@kestrelpictures</li>
    </ul>
  </section>
</main>
</body>
</html>
```